skyPARLOR Helicopter Tour WordPress Website Design

SkyPARLOR (skyparlor-example.com) is a premium helicopter tour company offering scenic flights in two Florida cities: Tampa and Sarasota. We are seeking a full Wordpress website redesign that is modern, upbeat, inviting, and highly conversion‑focused. The new site should feel energetic and trustworthy, reflect the excitement of helicopter sightseeing, and maintain our recognizable SkyPARLOR color palette—while updating the overall look to feel fresh, clean, and current.
The website must be SEO‑friendly, mobile‑optimized, and easy to navigate. It should highlight our 5‑star customer reviews, showcase our tours clearly, and integrate seamlessly with TrailDock for instant online booking. The design should support a premium aviation experience while remaining friendly and accessible to tourists, families, couples, and adventure seekers.

These elements are essential and must be included in the design:

Brand & UX:
- Modern, upbeat, inviting design
- SEO‑friendly structure and layout
- Easy navigation and clear user flow
- Light grey “SP” background logo watermark (as used on current site)
- Clean, aviation‑inspired typography and layout

Conversion Features:
- Instant booking above the fold (TrailDock integration)
- Live Orbin Ratings carousel
- Tour comparison table (duration, route, price, etc.)
- FAQ expandable section
- Gift Cards page (highlighted as a major offering)
- What to Expect timeline (Arrive → Check‑In → Safety Briefing → Flight → Photos)
- Weather transparency widget (clear messaging about weather‑dependent flights

Content Structure:
- Separate pages for Tampa, Sarasota, and Gender Reveal Flights
- Pilot/Team profiles with short bios
- Highlighted features:
- Doors‑Off option
- Sunset flights
- Romantic packages
- Champagne add‑ons

Colors:
Use the existing SkyPARLOR palette as the foundation, but modernize it.
- Background: Clean with the light grey “SP” watermark integrated tastefully.
The overall color direction should feel bright, premium, energetic, and trustworthy

Target Market(s)

Tourists visiting Tampa or Sarasota, Families looking for memorable activities, Couples seeking romantic experiences (sunset flights, proposals, anniversaries), Adventure seekers and content creators, Locals celebrating birthdays, holidays, or special occasions, Gender reveal clients looking for a unique aerial reveal experience

Industry/Entity Type

Travel & Tourism / Aviation / Helicopter Tours / Experience‑based Activities

Requirements
Must have
• These elements are essential and must be included in the design: Brand & UX - Modern, upbeat, inviting design / SEO‑friendly structure and layout / Easy navigation and clear user flow / Light grey “SP” background logo watermark (as used on current site) / Clean, aviation‑inspired typography and layout
Nice to have
• Interactive route map showing flight paths / Subtle motion or parallax effects in hero sections / Animated icons or micro‑interactions / Social media integration (Instagram grid, TikTok clips) / Sticky mobile booking bar / Video header or short aerial footage loop / Subtle aviation‑themed graphic elements (rotor blur, sky gradients, etc.
Should not have
• No dark, heavy, or overly moody themes / No outdated fonts or overly playful typography / No cluttered layouts or excessive text blocks / No stocky, generic tourism imagery / No slow‑loading animations or heavy effects that hurt SEO

```html
<!DOCTYPE html>
<html lang="en">
<head>
<meta charset="UTF-8">
<title>SkyPARLOR – Helicopter Tours Over Tampa And Sarasota</title>
<link href="https://fonts.googleapis.com/css2?family=Saira+Extra+Condensed:wght@300;400;600;700&family=Manrope:wght@400;500;600;700&display=swap" rel="stylesheet">
<style>
:root{
  --stage:#a3a7ab;
  --paper:#f2f3f5;
  --ink:#15171c;
  --ink-soft:#3a3d44;
  --muted:#6b6f78;
  --accent:#2b5aa8;
  --accent-bright:#3a6fc6;
  --line:#d9dce1;
  --watermark:#e0e2e6;
  --hero-top:#24232d;
  --hero-sky:#4a4550;
  --hero-glow:#c98a3a;
  --hero-water:#2a2833;
  --hero-deep:#0f0e14;
  --white:#ffffff;
}
*{margin:0;padding:0;box-sizing:border-box}
html,body{width:1200px;height:800px;overflow:hidden}
body{background:var(--stage);font-family:"Manrope",sans-serif;color:var(--ink);position:relative}
.display{font-family:"Saira Extra Condensed",sans-serif;text-transform:uppercase;letter-spacing:.01em;line-height:.95}
.display .light{font-weight:300}
.display .bold{font-weight:700}

.page{position:absolute;top:40px;width:560px;height:720px;background:var(--paper);overflow:hidden;box-shadow:0 18px 40px rgba(0,0,0,.18)}
.page--home{left:30px}
.page--continued{left:610px}

/* watermark */
.watermark{position:absolute;font-family:"Saira Extra Condensed",sans-serif;font-weight:700;color:var(--watermark);line-height:1;pointer-events:none;z-index:0}

/* hero */
.hero{position:relative;height:296px;color:var(--white)}
.hero__photo{position:absolute;inset:0;background:linear-gradient(180deg,var(--hero-top) 0%,var(--hero-sky) 22%,#6a5a52 34%,var(--hero-glow) 40%,#5a4c5a 46%,var(--hero-water) 62%,var(--hero-deep) 100%)}
.nav{position:relative;z-index:2;display:flex;align-items:center;height:40px;padding:0 30px;background:rgba(20,20,28,.35)}
.brand{font-size:9px;font-weight:600;letter-spacing:.04em;display:flex;align-items:center;gap:5px}
.brand__dot{width:12px;height:12px;border-radius:50%;background:var(--white)}
.nav__links{display:flex;gap:12px;margin-left:52px;font-size:6.5px;list-style:none}
.nav__links li{display:flex;align-items:center;gap:12px}
.nav__links li+li::before{content:"";width:2px;height:2px;border-radius:50%;background:var(--white);margin-left:-6px;margin-right:-6px}
.search{margin-left:auto;display:flex;align-items:center;gap:4px;font-size:6px;padding:4px 8px;border:1px solid rgba(255,255,255,.25);border-radius:10px;background:rgba(255,255,255,.06)}
.hero__content{position:relative;z-index:2;text-align:center;margin-top:78px}
.hero__title{font-size:42px}
.hero__sub{font-size:9px;margin-top:6px}
.hero__badges{display:flex;justify-content:center;gap:8px;margin-top:16px}
.badge{border:1px solid rgba(255,255,255,.3);border-radius:4px;background:rgba(10,10,15,.45);padding:6px 9px;display:flex;flex-direction:column;justify-content:center;min-height:28px}
.badge__main{font-family:"Saira Extra Condensed",sans-serif;font-weight:600;font-size:8.5px;text-transform:uppercase;display:flex;align-items:center;gap:4px}
.badge__small{font-size:4.5px;opacity:.75;margin-top:1px}
.social{position:absolute;right:30px;top:110px;z-index:2;display:flex;flex-direction:column;align-items:center;gap:10px}
.social__rule{width:1px;height:38px;background:rgba(255,255,255,.25)}
.social__dot{width:8px;height:8px;border-radius:50%;border:1.2px solid var(--white)}
.social__rule--tail{height:48px}

/* why */
.why{position:relative;padding:30px 30px 0;display:flex;justify-content:space-between;z-index:1}
.why__title{font-size:29px;color:var(--ink)}
.why__aside{width:200px;margin-right:18px}
.btn-book{display:inline-flex;align-items:center;gap:10px;border:1px solid var(--line);border-radius:16px;padding:4px 4px 4px 11px;font-size:10px;font-weight:500;background:var(--white)}
.btn-book__icon{width:20px;height:20px;border-radius:50%;background:var(--accent);display:flex;align-items:center;justify-content:center}
.why__text{font-size:8.5px;line-height:1.5;color:var(--ink-soft);margin-top:13px}
.video{position:relative;margin:30px 30px 0;height:200px;background:linear-gradient(180deg,#5b5e6e 0%,#4c5566 30%,#2f6c6e 60%,#1d4a4d 100%);z-index:1}
.video__play{position:absolute;left:50%;top:50%;width:34px;height:34px;margin:-17px 0 0 -17px;border-radius:50%;background:var(--white);display:flex;align-items:center;justify-content:center}
.section-heading{position:relative;z-index:1;text-align:center;font-size:30px}
.page--home .section-heading{position:absolute;left:0;right:0;bottom:10px}

/* continued page */
.intro{position:relative;z-index:1;text-align:center;padding-top:30px}
.intro__sub{font-size:9px;color:var(--ink-soft);margin-top:6px}
.tours{position:relative;z-index:1;display:grid;grid-template-columns:repeat(4,1fr);gap:9px;padding:0 30px;margin-top:26px}
.tour{display:flex;flex-direction:column;gap:6px}
.tour__img{height:140px}
.tour__name{font-family:"Saira Extra Condensed",sans-serif;font-weight:700;font-size:8.5px;text-transform:uppercase}
.tour__desc{font-size:5px;line-height:1.45;color:var(--ink-soft);margin-top:3px}
.tour__link{font-size:5px;font-weight:700;color:var(--accent);text-decoration:underline;margin-top:4px;display:flex;align-items:center;gap:3px}
.tour--offset{flex-direction:column}
.img-sea{background:linear-gradient(180deg,#cfe3f2 0%,#5fa8d6 35%,#2fb3b8 65%,#1e8e93 100%)}
.img-sky{background:linear-gradient(180deg,#9dbde4 0%,#c9dcef 60%,#e6eef7 100%)}
.img-sunset{background:linear-gradient(180deg,#f2b36b 0%,#d4785a 45%,#4a5878 100%)}
.img-gulf{background:linear-gradient(180deg,#bcd8ee 0%,#6bb0d8 50%,#3a8fa8 100%)}
.stats{position:relative;z-index:1;display:grid;grid-template-columns:repeat(4,1fr);gap:9px;padding:0 30px;margin-top:56px}
.stat__num{font-family:"Saira Extra Condensed",sans-serif;font-weight:600;font-size:30px;line-height:1;color:var(--ink)}
.stat__num--accent{color:var(--accent-bright)}
.stat__label{font-size:8.5px;color:var(--ink-soft);margin-top:6px}
.memories{position:relative;z-index:1;display:grid;grid-template-columns:repeat(3,1fr);grid-template-rows:83px 83px;gap:9px;padding:0 30px;margin-top:56px}
.memories__tall{grid-row:1 / span 2;grid-column:3}
.mem-night{background:linear-gradient(160deg,#3a3a40 0%,#1f2024 100%)}
.mem-pad{background:linear-gradient(160deg,#2a2a2d 0%,#1a1a1c 60%,#3b2a22 100%)}
.mem-city{background:linear-gradient(160deg,#8ea7c2 0%,#5f7790 60%,#3d4a58 100%)}
.mem-cockpit{background:linear-gradient(170deg,#9fc4e8 0%,#c5d6e6 40%,#5d6f82 100%)}
.page--continued .section-heading{margin-top:20px}
</style>
</head>
<body>

<main class="page page--home">
  <header class="hero">
    <div class="hero__photo" role="img" aria-label="Sunset over Tampa Bay with a long causeway bridge stretching across calm water"></div>
    <nav class="nav">
      <div class="brand"><span class="brand__dot"></span>SkyPARLOR</div>
      <ul class="nav__links">
        <li>Home</li><li>Tours</li><li>Experiences</li><li>Gift Cards</li><li>What to Expect</li><li>About</li>
      </ul>
      <div class="search">
        <svg width="6" height="6" viewBox="0 0 10 10" fill="none" stroke="#fff" stroke-width="1.4"><circle cx="4.2" cy="4.2" r="3.2"/><path d="M6.6 6.6 9 9"/></svg>
        Search Now
      </div>
    </nav>
    <div class="hero__content">
      <h1 class="hero__title display"><span class="light">See Florida</span><br><span class="light">Like </span><span class="bold">Never Before</span></h1>
      <p class="hero__sub">Premium Helicopter Tours Over Tampa And Sarasota.</p>
      <div class="hero__badges">
        <div class="badge">
          <span class="badge__main">
            <svg width="8" height="8" viewBox="0 0 10 10"><path d="M5 .6l1.3 2.8 3 .3-2.3 2 .7 3-2.7-1.6-2.7 1.6.7-3L.7 3.7l3-.3z" fill="#e9b23c"/></svg>
            5.0 Rated On Orbin
          </span>
        </div>
        <div class="badge">
          <span class="badge__main">FAA Certified Pilots</span>
          <span class="badge__small">Thousands of Happy Flyers</span>
        </div>
      </div>
    </div>
    <div class="social" aria-label="Social links">
      <span class="social__rule"></span>
      <span class="social__dot"></span>
      <span class="social__dot"></span>
      <span class="social__dot"></span>
      <span class="social__rule social__rule--tail"></span>
    </div>
  </header>

  <span class="watermark" style="left:14px;top:300px;font-size:70px">SP</span>

  <section class="why">
    <h2 class="why__title display"><span class="light">Why SkyPARLOR Is</span><br><span class="bold">Florida’s Most Trusted</span></h2>
    <div class="why__aside">
      <a class="btn-book">Book Your Tour
        <span class="btn-book__icon"><svg width="8" height="8" viewBox="0 0 10 10" fill="none" stroke="#fff" stroke-width="1.4"><path d="M2.5 7.5 7.5 2.5M3.5 2.5h4v4"/></svg></span>
      </a>
      <p class="why__text">We Deliver A Premium, Safe, And Memorable Aviation Experience From Takeoff To Landing.</p>
    </div>
  </section>

  <div class="video" role="img" aria-label="Aerial night view of the Sarasota marina and downtown skyline">
    <span class="video__play"><svg width="9" height="9" viewBox="0 0 10 10"><path d="M3 2l5 3-5 3z" fill="#15171c"/></svg></span>
  </div>

  <span class="watermark" style="left:60px;top:652px;font-size:48px">SP</span>
  <h2 class="section-heading display"><span class="light">Our Signature </span><span class="bold">Helicopter Experiences</span></h2>
</main>

<section class="page page--continued">
  <span class="watermark" style="left:20px;top:14px;font-size:60px">SP</span>
  <div class="intro">
    <h2 class="section-heading display"><span class="light">Our Signature </span><span class="bold">Helicopter Experiences</span></h2>
    <p class="intro__sub">Soar Above Beaches, Bays, And Iconic Landmarks.</p>
  </div>

  <div class="tours">
    <article class="tour">
      <div class="tour__img img-sunset" role="img" aria-label="Helicopter view of the Gulf coast at sunset"></div>
      <div>
        <h3 class="tour__name">Sunset Romance Flight</h3>
        <p class="tour__desc">Golden hour views with an optional champagne toast.</p>
        <span class="tour__link">VIEW DETAILS ↗</span>
      </div>
    </article>
    <article class="tour">
      <div>
        <h3 class="tour__name">Doors-Off Tampa Tour</h3>
        <p class="tour__desc">Open-air flying over the bay and the downtown skyline.</p>
        <span class="tour__link">VIEW DETAILS ↗</span>
      </div>
      <div class="tour__img img-gulf" role="img" aria-label="Open-door helicopter view above Tampa Bay"></div>
    </article>
    <article class="tour">
      <div class="tour__img img-sea" role="img" aria-label="Aerial view of a causeway crossing turquoise water and green islands"></div>
      <div>
        <h3 class="tour__name">Ultimate Florida Aerial Adventure</h3>
        <p class="tour__desc">The most immersive helicopter experience SkyPARLOR has to offer.</p>
        <span class="tour__link">VIEW DETAILS ↗</span>
      </div>
    </article>
    <article class="tour">
      <div>
        <h3 class="tour__name">Gender Reveal Celebration Flight</h3>
        <p class="tour__desc">Turn your special moment into an unforgettable aerial celebration.</p>
        <span class="tour__link">VIEW DETAILS ↗</span>
      </div>
      <div class="tour__img img-sky" role="img" aria-label="Small plane releasing pink and blue smoke in a cloudy blue sky"></div>
    </article>
  </div>

  <div class="stats">
    <div><p class="stat__num">10+</p><p class="stat__label">Years In The Air</p></div>
    <div><p class="stat__num">2</p><p class="stat__label">Florida Cities</p></div>
    <div><p class="stat__num">1,500+</p><p class="stat__label">Successful Tours</p></div>
    <div><p class="stat__num stat__num--accent">2,290+</p><p class="stat__label">5.0 Star Orbin Rating</p></div>
  </div>

  <div class="memories">
    <div class="mem-night" role="img" aria-label="Night flight over city lights seen from the cabin"></div>
    <div class="mem-night" role="img" aria-label="Passenger looking down at the city lights at night"></div>
    <div class="memories__tall mem-cockpit" role="img" aria-label="Pilot with headset flying above downtown towers"></div>
    <div class="mem-pad" role="img" aria-label="Helicopter parked on a marked landing pad"></div>
    <div class="mem-city" role="img" aria-label="Smiling passengers in headsets above the waterfront"></div>
  </div>

  <span class="watermark" style="left:130px;top:650px;font-size:48px">SP</span>
  <h2 class="section-heading display"><span class="light">We Create </span><span class="bold">Memories</span></h2>
</section>

</body>
</html>
```